Professional Services - letterhead / business cards

The company (velmora partners) will provide services to Investment Funds and large investors in Spain. I have recently chosen a logo that I am attaching.

I would like a simple stationary design that i could use as letter head, business cards and "with compliments" cards.

I am not quite sure which color I will mostly use for the logo, in the email signature I will probably lean towards the white background and grey letters. I am attaching my favourite options.

Target Market(s)

Large Multinationals, Investment funds and Law firms

Industry/Entity Type

Business

Requirements
Must have
• my details are:
Luis R. Abadal
Velmora Partners S.L.
Casa de Torrelumbre
Calle de Vientoalto 27
28014 Madrid
T: +34 (91) 387-2265
M: +34 (646) 819-054
e-mail: labadal@velmorapartners.com

```html
<!DOCTYPE html>
<html lang="es">
<head>
<meta charset="utf-8">
<title>Velmora Partners – Business Card</title>
<link rel="stylesheet" href="https://fonts.googleapis.com/css2?family=Arimo:wght@400;700&family=Questrial&display=swap">
<style>
  :root {
    --navy: #24266b;
    --white: #ffffff;
    --rule-grey: #b4b4b8;
    --text-grey: #4a4a50;
    --stage: #ecebe8;
  }
  * { box-sizing: border-box; margin: 0; padding: 0; }
  html, body { width: 1200px; height: 711px; overflow: hidden; }
  body {
    background: var(--stage);
    font-family: "Arimo", Arial, sans-serif;
    position: relative;
  }
  .card {
    position: absolute;
    top: 200px;
    width: 540px;
    height: 310px;
    box-shadow: 0 6px 18px rgba(0,0,0,0.18);
    overflow: hidden;
  }
  /* Front */
  .card-front { left: 45px; background: var(--white); }
  .front-header {
    height: 50px;
    background: var(--navy);
    color: var(--white);
    display: flex;
    align-items: flex-end;
    justify-content: center;
    gap: 6px;
    padding-bottom: 9px;
  }
  .holder-name { font-weight: 700; font-size: 19px; letter-spacing: 0.5px; }
  .holder-company { font-size: 12.5px; }
  .rule { height: 5px; background: var(--rule-grey); border-top: 2px solid var(--white); }
  .front-body { height: 202px; position: relative; }
  .brand-name {
    position: absolute;
    left: 0; right: 0; top: 48px;
    text-align: center;
    font-family: "Questrial", "Century Gothic", sans-serif;
    font-size: 48px;
    color: var(--navy);
    letter-spacing: 0.5px;
  }
  .contact-phones {
    position: absolute; left: 0; right: 0; top: 130px;
    display: flex; justify-content: center; gap: 20px;
    font-size: 13px; color: var(--text-grey);
  }
  .phone { display: flex; align-items: center; gap: 6px; }
  .phone svg { width: 11px; height: 12px; fill: var(--navy); }
  .contact-email {
    position: absolute; left: 0; right: 0; top: 160px;
    text-align: center;
    font-size: 13px; letter-spacing: 2.6px; color: var(--text-grey);
  }
  .front-footer {
    height: 48px;
    background: var(--navy);
    color: var(--white);
    font-size: 12.5px;
    display: flex; align-items: center; justify-content: center;
    border-top: 2px solid var(--white);
  }
  /* Back */
  .card-back {
    left: 615px;
    background: var(--navy);
    color: var(--white);
  }
  .card-back .brand-name {
    color: var(--white);
    top: 105px;
  }
  .web-address {
    position: absolute; left: 0; right: 0; top: 228px;
    text-align: center;
    font-family: "Questrial", "Century Gothic", sans-serif;
    font-size: 15px; letter-spacing: 6px; font-weight: 700;
  }
</style>
</head>
<body>
  <section class="card card-front" aria-label="Business card front">
    <header class="front-header">
      <span class="holder-name">Luis R. Abadal,</span>
      <span class="holder-company">Velmora Partners S.L.</span>
    </header>
    <div class="rule"></div>
    <div class="front-body">
      <div class="brand-name">velmora partners</div>
      <div class="contact-phones">
        <span class="phone">
          <svg viewBox="0 0 12 12" aria-hidden="true"><path d="M3 0.5l2 2.5-1.2 1.3c.6 1.5 1.8 2.8 3.4 3.5L8.5 6.5 11.5 8.5 10.5 11C5.5 11 1 6.5 1 1.5z"/></svg>
          +34 (91) 387-2265
        </span>
        <span class="phone">
          <svg viewBox="0 0 12 12" aria-hidden="true"><path d="M3 0h6v12H3z M4 1.5v6h4v-6z" fill-rule="evenodd"/></svg>
          +34 (646) 819-054
        </span>
      </div>
      <div class="contact-email">labadal@velmorapartners.com</div>
    </div>
    <div class="rule"></div>
    <footer class="front-footer">Casa de Torrelumbre, Calle de Vientoalto 27, 28014 Madrid</footer>
  </section>

  <section class="card card-back" aria-label="Business card back">
    <div class="brand-name">velmora partners</div>
    <div class="web-address">www.velmora.com</div>
  </section>
</body>
</html>
```